Stationery Design Project

We need a stationery design for our Norwegian trucking company. We have existed for about 15 years and our 12 drivers uses relatively new vehicles to transport goods around in northern Norway. Long distance routes with fresh fish og food transport is our main operations.

We have already made alogo that's printed on our trucks. The logo and a picture of our trucks is attached. I think the logo i crappy, but since its already in use, changing it is not an option in this round. Still using a better colour scheme in the overall stationery and more interesting fonts is possible (altso in the logo).

Company details:
Name: Kjelvraket AS
Organisation nr 873 615 309
Post adress: 8642 Raudvik

I like minimalism and simplicity. I am avalibly for questions in normal GMT working hours either here or on mail: ivar@fjordlast.no

Reason: Hi. Im extending the deadline because I needed some time to find a vector file of our logo. Sorry for the inconvenience

Hi, and thanks for all your interest in the project. Some updates:

-          I have decided to commit to using one of the designs. Some designer will get the payment.

-          I have extended the deadline with 24 hours since I needed some time to find our firms vector logo (a slow Swedish man was holding me up)

-          We will not choose a design before the deadline. No need to rush.

-          We have received a lot of great design and think there is a need to specified the product we want to make:

o   Business Card for all our employers. I just need the design and will duplicate with the correct numbers and name myself. The information on should be: Logo, employer’s name, Phone number, email, website, Postal number and address. Use this as a template: logo, Leif Brattvoll, 47382066, Leif@fjordlast.no,, fjordlast.no, 8642 Raudvik. The order and placement of the information is your creative decision.

o   Stickers to put on the goods we travel. On the sticker the should be the following information: Logo, phone number, Tekst and link: Fraktæ av Kjelvraket. Ke du syns? Fjordlast.no/tilbakemelding (this means: Handled by Kjelvraket. What do you think Fjordlast.no/feedback -à the link will be a feedback form). The placement the information and size is your creative decision with some stings: we have been thinking of using Drukko for printing and see that a size about 6x6 cm, 8x5 or something like that. (with 3000 copies our budget is 200 punds). Any suggestions of other suppliers are welcome. Drukko price calculator http://www.drukkolabelhouse.co.uk/digital-litho-printing/printing-labels-tags/stickers/

o   Letterhead with logo, address, phone number and organizational number.

o   Envelopes with logo,address, phone number and organizational number.

Have a nice day.

 

 

• Using the blue colour in the logo and using a similar graphic approch.

```html
<!DOCTYPE html>
<html lang="no">
<head>
<meta charset="utf-8">
<title>Kjelvraket – visittkort</title>
<link rel="stylesheet" href="https://fonts.googleapis.com/css2?family=Open+Sans:wght@400;600;700&display=swap">
<style>
  :root {
    --stage: #e4e6e9;
    --paper: #ffffff;
    --navy: #0b4fa6;
    --blue: #0a72bb;
    --brand: #0b5ea8;
    --name: #0a6ab0;
    --ink: #2a2a2a;
    --edge: #9aa0a6;
  }
  * { box-sizing: border-box; margin: 0; padding: 0; }
  html, body { width: 1200px; height: 751px; overflow: hidden; }
  body {
    background: var(--stage);
    font-family: "Open Sans", Arial, sans-serif;
    position: relative;
  }
  .card {
    position: absolute;
    width: 524px;
    height: 298px;
    border-radius: 18px;
    overflow: hidden;
  }
  .card--front { left: 64px; top: 52px; background: var(--paper); border: 1px solid var(--edge); }
  .card--navy { left: 620px; top: 52px; background: var(--navy); }
  .card--white { left: 64px; top: 393px; background: var(--paper); border: 1px solid var(--edge); }
  .card--blue { left: 620px; top: 393px; background: var(--blue); }

  .swoosh { position: absolute; inset: 0; width: 100%; height: 100%; }

  .brand {
    position: absolute;
    display: flex;
    align-items: center;
    gap: 14px;
    font-weight: 700;
    font-size: 50px;
    line-height: 1;
    letter-spacing: -0.5px;
    color: var(--brand);
  }
  .brand__dot {
    width: 30px; height: 30px; border-radius: 50%;
    background: currentColor;
  }
  .card--front .brand { left: 34px; top: 58px; font-size: 46px; }
  .card--navy .brand, .card--blue .brand { color: #fff; }
  .card--navy .brand, .card--blue .brand, .card--white .brand {
    left: 0; right: 0; top: 124px; justify-content: center;
  }

  .website {
    position: absolute;
    left: 0; right: 0;
    top: 248px;
    text-align: center;
    font-size: 17px;
    letter-spacing: 3.4px;
    color: #fff;
  }
  .card--white .website { color: var(--ink); }

  .holder {
    position: absolute;
    left: 32px; top: 166px;
  }
  .holder__name {
    font-size: 19px;
    font-weight: 700;
    color: var(--name);
  }
  .holder__address {
    margin-top: 8px;
    font-size: 14px;
    color: var(--ink);
    display: flex; align-items: center; gap: 5px;
  }

  .contact {
    position: absolute;
    right: 24px; top: 196px;
    list-style: none;
    text-align: right;
    color: #fff;
    font-size: 14px;
    line-height: 21.5px;
  }
  .contact li { display: flex; justify-content: flex-end; align-items: center; gap: 5px; }
  .icon { width: 11px; height: 11px; flex: none; }
</style>
</head>
<body>

  <section class="card card--front" aria-label="Visittkort, forside">
    <svg class="swoosh" viewBox="0 0 524 298" aria-hidden="true">
      <path d="M524 14 C470 112 350 228 0 240 L0 298 L524 298 Z" fill="var(--blue)"/>
      <path d="M0 224 C150 244 300 214 372 164 C300 232 150 262 0 264 Z" fill="#fff"/>
      <path d="M0 232 C150 250 300 222 366 172 C300 238 150 260 0 258 Z" fill="var(--navy)"/>
    </svg>

    <div class="brand"><span class="brand__dot"></span>Kjelvraket</div>

    <div class="holder">
      <p class="holder__name">Leif Brattvoll</p>
      <p class="holder__address">
        <svg class="icon" viewBox="0 0 12 12" aria-hidden="true"><path d="M1 6 L6 2 L11 6 V11 H1 Z" fill="var(--name)"/><rect x="3" y="7" width="6" height="1" fill="#fff"/><rect x="3" y="9" width="6" height="1" fill="#fff"/></svg>
        8642 Raudvik
      </p>
    </div>

    <ul class="contact">
      <li>
        <svg class="icon" viewBox="0 0 12 12" aria-hidden="true"><path d="M3 1 L5 3.5 L4 5 C4.8 6.6 5.6 7.4 7 8 L8.5 7 L11 9 L9.5 11 C5 10.5 1.5 7 1 2.5 Z" fill="#fff"/></svg>
        47382066
      </li>
      <li>Org nr 873 615 309</li>
      <li>
        <svg class="icon" viewBox="0 0 12 12" aria-hidden="true"><rect x="1" y="3" width="10" height="7" fill="#fff"/><path d="M1 3 L6 7 L11 3" fill="none" stroke="var(--blue)" stroke-width="1"/></svg>
        Leif@fjordlast.no
      </li>
      <li>
        <svg class="icon" viewBox="0 0 12 12" aria-hidden="true"><circle cx="6" cy="6" r="4.8" fill="none" stroke="#fff" stroke-width="1.2"/><path d="M1.2 6 H10.8 M6 1.2 V10.8" stroke="#fff" stroke-width="1"/></svg>
        www.fjordlast.no
      </li>
    </ul>
  </section>

  <section class="card card--navy" aria-label="Visittkort, bakside mørkeblå">
    <div class="brand"><span class="brand__dot"></span>Kjelvraket</div>
    <p class="website">www.fjordlast.no</p>
  </section>

  <section class="card card--white" aria-label="Visittkort, bakside hvit">
    <div class="brand"><span class="brand__dot"></span>Kjelvraket</div>
    <p class="website">www.fjordlast.no</p>
  </section>

  <section class="card card--blue" aria-label="Visittkort, bakside blå">
    <div class="brand"><span class="brand__dot"></span>Kjelvraket</div>
    <p class="website">www.fjordlast.no</p>
  </section>

</body>
</html>
```